Animal Eye Clinic needs a Business card

We are a new veterinary ophthalmology practice (Ridgeline Pet Vision Care) and we need a business card designed. We only see animal eyes - we are not a regular veterinary clinic. We already have a logo. We are looking for a professional, good looking business card to hand out to our clients. We are looking for something simple but professional and contemporary. Our logo is likely the only picture/graphic that needs to be on the card.
Updates

Contact Information for Business Card

Delia Vossman, BSc, DVM, MSc, DipACVO
Veterinary Ophthalmologist

Phone: 250.418.3927
Email: ridgelinepetvisioncare@mailbox-example.net
Website: ridgelinepetvisioncare-example.net
Address: 1874 Thornbury Rd
Kelowna, BC, V1X 4M9

Colors

Designer to choose colors to be used in the design.

Requirements
Must have
• Our logo (attached)

```html
<!DOCTYPE html>
<html lang="en">
<head>
<meta charset="utf-8">
<title>Ridgeline Pet Vision Care – Business Card</title>
<link rel="stylesheet" href="https://fonts.googleapis.com/css2?family=Montserrat:wght@400;500;600;700&display=swap">
<style>
  :root {
    --backdrop: #e6e4e1;
    --card-white: #ffffff;
    --card-grey: #737273;
    --teal: #1a9dad;
    --ink: #5b5b5d;
    --rule: #8a8a8c;
    --band-line: #8d8d8f;
  }
  * { box-sizing: border-box; margin: 0; padding: 0; }
  html, body {
    width: 1200px; height: 852px; overflow: hidden;
    background: var(--backdrop);
    font-family: "Montserrat", sans-serif;
  }
  .stage { position: relative; width: 1200px; height: 852px; }

  .card {
    position: absolute;
    width: 560px; height: 320px;
    border-radius: 18px;
    overflow: hidden;
    box-shadow: 0 10px 24px rgba(0,0,0,.22);
  }

  /* Back of card */
  .card-back { left: 50px; top: 70px; background: var(--card-grey); }
  .card-back .brand { position: absolute; right: 70px; top: 118px; color: var(--card-white); }

  /* Brand lockup (shared) */
  .brand { display: flex; align-items: center; gap: 12px; font-weight: 700; }
  .brand-dot { width: 46px; height: 46px; border-radius: 50%; background: currentColor; flex: none; }
  .brand-name { line-height: 1.1; }
  .brand-name .top { display: block; font-size: 12px; letter-spacing: 7px; }
  .brand-name .bottom { display: block; font-size: 20px; letter-spacing: .3px; }

  /* Front of card */
  .card-front { left: 590px; top: 470px; background: var(--card-white); }
  .card-front .brand { position: absolute; left: 30px; top: 98px; color: var(--teal); }
  .card-front .brand-name .bottom { font-size: 17px; }

  .divider { position: absolute; left: 286px; top: 44px; width: 1px; height: 150px; background: var(--rule); }

  .contact { position: absolute; left: 302px; top: 40px; color: var(--ink); }
  .person-name { color: var(--teal); font-weight: 600; font-size: 23px; letter-spacing: .2px; }
  .credentials, .role { font-size: 10.5px; margin-top: 3px; font-weight: 500; }
  .details { list-style: none; margin-top: 16px; font-size: 9px; font-weight: 500; }
  .details li { display: flex; align-items: center; gap: 7px; margin-bottom: 7px; }
  .details svg { width: 10px; height: 10px; flex: none; fill: var(--teal); }
  .details .phone { font-size: 12px; }
  .details .web-domain { color: var(--teal); }

  .band { position: absolute; left: 0; top: 0; width: 560px; height: 320px; }
  .band-address { font-size: 11.5px; font-weight: 500; fill: var(--card-white); letter-spacing: .4px; }
</style>
</head>
<body>
<main class="stage">

  <section class="card card-back" aria-label="Business card back">
    <div class="brand">
      <span class="brand-dot"></span>
      <span class="brand-name"><span class="top">RIDGELINE</span><span class="bottom">PET VISION CARE</span></span>
    </div>
  </section>

  <section class="card card-front" aria-label="Business card front">
    <svg class="band" viewBox="0 0 560 320" aria-hidden="true">
      <defs>
        <path id="address-curve" d="M150 316 Q300 206 548 186"/>
      </defs>
      <path d="M0 320 Q170 190 560 172" fill="none" stroke="var(--band-line)" stroke-width="3"/>
      <path d="M12 320 Q180 196 560 180 L560 320 Z" fill="var(--teal)"/>
      <text class="band-address"><textPath href="#address-curve" startOffset="4%">1874 Thornbury Rd Kelowna, BC, V1X 4M9</textPath></text>
    </svg>

    <div class="brand">
      <span class="brand-dot"></span>
      <span class="brand-name"><span class="top">RIDGELINE</span><span class="bottom">PET VISION CARE</span></span>
    </div>

    <div class="divider"></div>

    <div class="contact">
      <h1 class="person-name">Delia Vossman</h1>
      <p class="credentials">BSc, DVM, MSc, DipACVO</p>
      <p class="role">Veterinary Ophthalmologist</p>
      <ul class="details">
        <li class="phone">
          <svg viewBox="0 0 24 24"><path d="M6.6 10.8a15.1 15.1 0 0 0 6.6 6.6l2.2-2.2c.3-.3.7-.4 1-.2 1.1.4 2.3.6 3.6.6.6 0 1 .4 1 1V20c0 .6-.4 1-1 1A17 17 0 0 1 3 4c0-.6.4-1 1-1h3.5c.6 0 1 .4 1 1 0 1.3.2 2.5.6 3.6.1.3 0 .7-.2 1z"/></svg>
          250.418.3927
        </li>
        <li>
          <svg viewBox="0 0 24 24"><path d="M2 5h20v14H2zm2 2v.5l8 5 8-5V7z"/></svg>
          ridgelinepetvisioncare@mailbox-example.net
        </li>
        <li>
          <svg viewBox="0 0 24 24"><circle cx="12" cy="12" r="10"/></svg>
          <span>www.<span class="web-domain">ridgelinepetvisioncare-example</span>.net</span>
        </li>
      </ul>
    </div>
  </section>

</main>
</body>
</html>
```